Seeking a new website design for electrical contracting company

Brisket & Vane electrical contracting needs a new website for brisket-vane.example

We are looking for modern and something real cool with motion for a landing page. we have some cool images from our photo shoot. maybe even 3d motion our existing logo. we would like something we can edit with news and events and update a past project page. Also allow to take payment
stock images at
https://lorapellwinphotos.picvault-demo.example/Brisket-and-Vane

Target Market(s)

construction , home owners , business owners,

Industry/Entity Type

construction , electrical

Coding

Number of Pages Required

5+ page

Font styles to use
Serif
Sans Serif

Colors
0054AA
0677BA
7BADD7
CADEEF
E8F1F8
0094D4
00A9DD
6FCCEA
C7EBF8
E9F6FB
FFF300
FFF600
FEFA6F
FFFEC7
FFFEE8

Requirements
Must have
• excitement, motion, selling professionalism,

```html
<!DOCTYPE html>
<html lang="en">
<head>
<meta charset="utf-8">
<title>Brisket &amp; Vane — Electrical Contracting</title>
<link rel="stylesheet" href="https://fonts.googleapis.com/css2?family=Josefin+Sans:wght@400;600;700&display=swap">
<style>
:root{
  --navy:#273585;
  --navy-dark:#1d2766;
  --orange:#f7941d;
  --orange-soft:#f9a94a;
  --white:#ffffff;
  --ink:#2b2f45;
  --gray:#6b6f80;
  --mist:#e8eaf4;
  --line:#d6d8e2;
}
*{box-sizing:border-box;margin:0;padding:0}
html,body{width:1200px;height:4926px;overflow:hidden}
body{position:relative;background:var(--white);font-family:"Josefin Sans",sans-serif;color:var(--ink)}
.abs{position:absolute}

/* header */
.site-header{position:absolute;left:0;top:0;width:1200px;height:76px;background:var(--white);z-index:5}
.brand{position:absolute;display:flex;align-items:center;gap:10px;font-weight:700;color:var(--navy);text-transform:uppercase}
.brand-mark{width:42px;height:42px;background:var(--navy);border-radius:6px}
.header-brand{left:67px;top:17px;font-size:21px}
.main-nav a{position:absolute;top:31px;font-size:13px;font-weight:700;color:var(--navy-dark);text-decoration:none;transform:translateX(-50%)}
.header-phone{position:absolute;right:0;top:0;width:230px;height:76px;background:var(--orange);clip-path:polygon(22px 0,100% 0,100% 100%,0 100%);display:flex;align-items:center;gap:10px;padding-left:40px;color:var(--white);font-weight:700;font-size:17px}
.icon-dot{width:28px;height:28px;border-radius:50%;background:var(--white);display:flex;align-items:center;justify-content:center;flex:none}

/* hero */
.hero{position:absolute;left:0;top:76px;width:1200px;height:720px;
  background:
    radial-gradient(ellipse 420px 260px at 22% 82%,rgba(255,90,200,.45),transparent 70%),
    radial-gradient(ellipse 460px 280px at 78% 78%,rgba(80,220,255,.42),transparent 70%),
    radial-gradient(ellipse 600px 220px at 50% 62%,rgba(180,140,255,.35),transparent 70%),
    linear-gradient(180deg,#2a3c9c 0%,#3550bd 30%,#4c5ccc 55%,#5b4fb8 72%,#2f3a8e 88%,#1f2a6e 100%)}
.hero-title{position:absolute;top:100px;width:1200px;text-align:center;color:var(--white);font-size:70px;font-weight:700;letter-spacing:1px}
.hero-sub{position:absolute;top:188px;width:1200px;text-align:center;color:var(--white);font-size:31px;letter-spacing:1px}
.btn{display:inline-flex;align-items:center;justify-content:center;border-radius:30px;font-weight:700;text-decoration:none;letter-spacing:.5px}
.btn-quote{position:absolute;left:523px;top:238px;width:168px;height:40px;background:var(--orange);color:var(--white);font-size:12px}

/* section heading */
.section-head{position:absolute;width:1200px;text-align:center}
.head-mark{display:block;width:34px;height:34px;margin:0 auto 12px;border:3px solid var(--navy);border-radius:50%}
.section-title{font-size:41px;font-weight:700;color:var(--navy)}
.section-title .accent{color:var(--orange)}
.divider{display:block;margin:8px auto 0;width:130px;height:3px;background:var(--orange)}

/* services */
.service-card{position:absolute;top:894px;width:263px;height:272px}
.service-card .label{position:absolute;left:18px;bottom:24px;color:var(--white);font-size:19px;font-weight:700}
.service-card.featured{top:880px;height:308px;background:linear-gradient(160deg,#f7941d,#f39a2c 60%,#e98618)}
.service-card.featured .label{top:88px;bottom:auto;left:36px}
.service-card.featured p{position:absolute;top:120px;left:36px;right:26px;color:var(--white);font-size:12.5px;line-height:19px}
.svc-substation{background:linear-gradient(180deg,#d9dee8 0%,#9aa6bd 40%,#c98a4a 62%,#4a5a8a 85%,#2f3d7a 100%)}
.svc-engineer{background:linear-gradient(180deg,#cfe3f3 0%,#9cc2e2 35%,#c9d86a 62%,#4d6a9a 85%,#2f3d7a 100%)}
.svc-thermal{background:linear-gradient(180deg,#7b8fb5 0%,#2f5fb0 35%,#d8b07a 60%,#3a4f90 85%,#273585 100%)}

/* about */
.about-text{position:absolute;left:613px;top:1306px;width:540px}
.about-text h2{font-size:46px;line-height:44px;font-weight:700;color:var(--navy);text-transform:uppercase}
.about-text h2 span{color:var(--orange);display:block}
.about-text p{font-size:21px;line-height:28px;color:var(--ink);margin-top:22px}
.btn-navy{background:var(--navy);color:var(--white);font-size:13px;width:176px;height:46px;margin-top:40px}

/* mission / why */
.panel{position:absolute;top:1792px;width:600px;height:593px;color:var(--white);text-align:center}
.panel-mission{left:0;clip-path:polygon(0 0,100% 77px,100% 511px,0 593px);
  background:
    radial-gradient(ellipse 300px 200px at 30% 85%,rgba(255,230,150,.45),transparent 70%),
    radial-gradient(ellipse 260px 160px at 75% 30%,rgba(255,200,120,.35),transparent 70%),
    linear-gradient(160deg,#f7941d,#f6a23c 45%,#ee8a1e 70%,#d9761a)}
.panel-why{left:600px;clip-path:polygon(0 77px,100% 0,100% 593px,0 511px);
  background:
    radial-gradient(ellipse 280px 180px at 70% 25%,rgba(110,140,230,.35),transparent 70%),
    linear-gradient(200deg,#34449a,#273585 50%,#1f2a72)}
.panel h3{position:absolute;top:163px;width:100%;font-size:33px;font-weight:700}
.panel .rule{position:absolute;top:210px;left:50%;width:52px;height:3px;margin-left:-26px;background:var(--white)}
.panel p{position:absolute;top:236px;left:60px;right:60px;font-size:18.5px;line-height:23px;font-weight:400}
.btn-outline{position:absolute;top:2172px;width:166px;height:40px;border:2px solid var(--white);color:var(--white);font-size:12px}
.center-ring{position:absolute;left:572px;top:2045px;width:56px;height:56px;border:4px solid var(--white);border-radius:50%}

/* projects */
.project{position:absolute}
.slider-dots{position:absolute;top:3122px;left:533px;display:flex;gap:14px}
.slider-dots span{width:40px;height:4px;background:#c9ccd8}
.slider-dots span.on{background:var(--navy)}

/* news */
.news-band{position:absolute;left:0;top:3191px;width:1200px;height:688px;background:var(--mist)}
.news-head{position:absolute;left:100px;top:3262px}
.news-head h2{font-size:41px;font-weight:700;color:var(--navy);display:flex;align-items:center;gap:12px}
.news-head h2 .accent{color:var(--orange)}
.news-head .mark{width:30px;height:30px;border:3px solid var(--navy);border-radius:50%}
.news-head .divider{margin:8px 0 0;width:130px}
.news-main{position:absolute;left:103px;top:3367px;width:480px;height:390px;
  background:
    radial-gradient(ellipse 200px 180px at 85% 35%,rgba(255,235,190,.75),transparent 70%),
    linear-gradient(170deg,#c9bf9c,#8c8f7e 35%,#c7c85a 55%,#3d4a7a 80%,#2b3672)}
.news-main .caption{position:absolute;left:0;bottom:0;width:100%;padding:28px 32px 24px;background:linear-gradient(0deg,rgba(39,53,133,.95),rgba(39,53,133,.6));color:var(--white)}
.news-main h4{font-size:18px;font-weight:700}
.news-main p{font-size:13px;line-height:17px;margin-top:8px}
.news-item{position:absolute;left:596px;width:512px;height:187px;background:var(--white);border:1px solid var(--line)}
.news-item .thumb{position:absolute;left:0;top:0;width:245px;height:185px}
.news-item .body{position:absolute;left:262px;top:28px;right:14px}
.date-badge{display:inline-block;background:var(--orange);color:var(--white);font-size:10px;font-weight:700;padding:5px 10px 3px}
.news-item h5{font-size:15px;line-height:17px;color:var(--navy);font-weight:700;margin-top:10px}
.news-item p{font-size:11px;line-height:15px;color:var(--gray);margin-top:8px}

/* contact */
.contact{position:absolute;left:0;top:3879px;width:1200px;height:720px;
  background:
    radial-gradient(ellipse 260px 300px at 22% 72%,rgba(70,90,170,.55),transparent 70%),
    radial-gradient(ellipse 240px 280px at 48% 70%,rgba(60,80,160,.5),transparent 70%),
    linear-gradient(180deg,#2d3a8c,#263380 60%,#28357f)}
.contact-info{position:absolute;left:130px;top:3982px;width:440px;color:var(--white)}
.eyebrow{font-size:16px;letter-spacing:3px}
.contact-info h2{font-size:34px;font-weight:700;margin-top:10px;display:flex;align-items:center;gap:10px}
.contact-info h2 .mark{width:28px;height:28px;border:3px solid var(--white);border-radius:50%}
.contact-info .divider{margin:8px 0 0;width:110px}
.contact-info .lead{font-size:15.5px;line-height:20px;margin-top:22px}
.contact-line{display:flex;align-items:flex-start;gap:14px;font-size:20px;line-height:24px;margin-top:22px}
.contact-line .icon-dot{width:34px;height:34px}
.form-box{position:absolute;left:583px;top:3967px;width:535px;height:419px;background:var(--orange)}
.field{position:absolute;background:var(--white);height:46px;display:flex;align-items:center;gap:8px;padding-left:16px;font-size:14px;color:var(--ink)}
.btn-send{position:absolute;left:44px;top:338px;width:191px;height:42px;background:var(--navy);color:var(--white);font-size:13px;border-radius:0}

/* footer */
.footer-brand{position:absolute;top:4530px;width:1200px;display:flex;flex-direction:column;align-items:center;gap:14px;font-size:30px;font-weight:700;color:var(--navy)}
.footer-brand .brand-mark{width:64px;height:64px}
.footer-rule{position:absolute;left:130px;width:990px;height:1px;background:var(--line)}
.footer-nav{position:absolute;top:4700px;left:195px;width:830px;display:flex;justify-content:space-between;align-items:center;font-size:15px;font-weight:700;color:var(--navy-dark)}
.footer-nav .sep{width:5px;height:5px;border-radius:50%;background:var(--orange)}
.footer-contact{position:absolute;top:4780px;display:flex;align-items:center;gap:12px}
.footer-contact .circle{width:36px;height:36px;border-radius:50%;background:var(--orange);display:flex;align-items:center;justify-content:center}
.footer-contact .k{font-size:14px;color:var(--navy);font-weight:600}
.footer-contact .v{font-size:14px;color:var(--navy)}
.vsep{position:absolute;top:4780px;width:1px;height:40px;background:var(--line)}
.bottom-bar{position:absolute;left:0;top:4863px;width:1200px;height:63px;background:var(--navy-dark)}
.copyright{position:absolute;left:168px;top:24px;font-size:12px;color:var(--white)}
.copyright u{color:var(--white)}
.socials{position:absolute;left:990px;top:20px;display:flex;gap:6px}
.socials span{width:22px;height:22px;border-radius:50%;background:var(--white)}
.socials span:first-child{background:var(--orange)}
</style>
</head>
<body>

<header class="site-header">
  <div class="brand header-brand"><span class="brand-mark"></span>Brisket &amp; Vane</div>
  <nav class="main-nav">
    <a style="left:367px">HOME</a>
    <a style="left:472px">ABOUT US</a>
    <a style="left:590px">SERVICES</a>
    <a style="left:707px">PROJECTS</a>
    <a style="left:814px">NEWS</a>
    <a style="left:919px">CONTACT</a>
  </nav>
  <div class="header-phone">
    <span class="icon-dot"><svg width="16" height="16" viewBox="0 0 24 24"><path fill="#f7941d" d="M6.6 10.8a15 15 0 0 0 6.6 6.6l2.2-2.2a1 1 0 0 1 1-.25 11.4 11.4 0 0 0 3.6.57 1 1 0 0 1 1 1V20a1 1 0 0 1-1 1A17 17 0 0 1 3 4a1 1 0 0 1 1-1h3.5a1 1 0 0 1 1 1c0 1.25.2 2.45.57 3.57a1 1 0 0 1-.25 1z"/></svg></span>
    1-555-014-2290
  </div>
</header>

<section class="hero" role="img" aria-label="Night city skyline with glowing circuit lines rising into the sky">
  <h1 class="hero-title">BRISKET &amp; VANE</h1>
  <p class="hero-sub">ELECTRICAL CONTRACTING</p>
  <a class="btn btn-quote">GET A QUOTE &rsaquo;</a>
</section>
<svg class="abs" style="left:0;top:640px" width="1200" height="170" viewBox="0 0 1200 170">
  <polygon fill="#1d2766" points="0,100 592,22 592,32 0,140"/>
  <polygon fill="#f7941d" points="592,22 1200,100 1200,140 592,32"/>
  <polygon fill="#ffffff" points="0,143 592,32 1200,143 1200,170 0,170"/>
</svg>

<div class="section-head" style="top:728px">
  <span class="head-mark"></span>
  <h2 class="section-title">SERVICE <span class="accent">PROVIDES</span></h2>
  <span class="divider"></span>
</div>

<div class="service-card svc-substation" style="left:67px" role="img" aria-label="Electrician working on a high-voltage substation"><span class="label">| SERVICE HEADING</span></div>
<div class="service-card featured" style="left:333px"><span class="label">| SERVICE HEADING</span><p>Lorem ipsum dolor sit amet, consectetur adipiscing elit, sed do eiusmod tempor incididunt ut labore et dolore magna</p></div>
<div class="service-card svc-engineer" style="left:608px" role="img" aria-label="Engineer in hard hat holding a tablet"><span class="label">| SERVICE HEADING</span></div>
<div class="service-card svc-thermal" style="left:875px" role="img" aria-label="Thermal camera inspecting an electrical panel"><span class="label">| SERVICE HEADING</span></div>

<svg class="abs" style="left:76px;top:1232px" width="480" height="546" viewBox="0 0 480 546" role="img" aria-label="City at night with power pylon, framed in a hexagon">
  <defs>
    <linearGradient id="hexFill" x1="0" y1="0" x2="0" y2="1"><stop offset="0" stop-color="#5b74d8"/><stop offset=".45" stop-color="#3a50b0"/><stop offset=".75" stop-color="#2a3a8a"/><stop offset="1" stop-color="#1d2766"/></linearGradient>
    <radialGradient id="hexGlow" cx=".5" cy=".82" r=".4"><stop offset="0" stop-color="#6fe0ff" stop-opacity=".55"/><stop offset="1" stop-color="#6fe0ff" stop-opacity="0"/></radialGradient>
  </defs>
  <polygon points="240,4 476,140 476,406 240,542 4,406 4,140" fill="none" stroke="#3a4aa0" stroke-width="2"/>
  <polygon points="240,42 440,158 440,388 240,504 40,388 40,158" fill="url(#hexFill)"/>
  <polygon points="240,42 440,158 440,388 240,504 40,388 40,158" fill="url(#hexGlow)"/>
</svg>

<div class="about-text">
  <h2>About <span>Brisket &amp; Vane</span></h2>
  <span class="divider" style="margin:10px 0 0;width:110px"></span>
  <p>Lorem ipsum dolor sit amet, consectetur adipiscing elit, sed do eiusmod tempor incididunt</p>
  <p>At labore et dolore magna aliqua. Ut enim ad minim veniam, quis nostrud exercitation ullamco laboris nisi ut aliquip ex ea commodo consequat. Duis aute irure dolor in reprehend</p>
  <a class="btn btn-navy">LEARN MORE &rsaquo;</a>
</div>

<div class="panel panel-mission" role="img" aria-label="Orange-toned city at dusk">
  <h3>OUR MISSION</h3><span class="rule"></span>
  <p>Lorem ipsum dolor sit amet, consectetur adipiscing elit, sed do eiusmod tempor incididunt ut labore et dolore magna aliqua. Ut enim ad minim veniam, quis nostrud exercitation ullamco laboris nisi ut aliquip ex ea commodo.</p>
</div>
<div class="panel panel-why" role="img" aria-label="Blue-toned power lines at dusk">
  <h3>WHY CHOOSE US</h3><span class="rule"></span>
  <p>Lorem ipsum dolor sit amet, consectetur adipiscing elit, sed do eiusmod tempor incididunt ut labore et dolore magna aliqua. Ut enim ad minim veniam, quis nostrud exercitation ullamco laboris nisi ut aliquip ex ea commodo.</p>
</div>
<a class="btn btn-outline" style="left:212px">LEARN MORE &rsaquo;</a>
<a class="btn btn-outline" style="left:835px">LEARN MORE &rsaquo;</a>
<span class="center-ring"></span>

<div class="section-head" style="top:2398px">
  <span class="head-mark"></span>
  <h2 class="section-title">RECENT <span class="accent">PROJECTS</span></h2>
  <span class="divider"></span>
</div>
<div class="project" style="left:94px;top:2544px;width:332px;height:244px;background:linear-gradient(180deg,#8fa6cf 0%,#5a74a8 40%,#3f5a3a 70%,#1f2b4a 100%)" role="img" aria-label="Engineer with laptop near a substation at dusk"></div>
<div class="project" style="left:441px;top:2544px;width:333px;height:244px;background:linear-gradient(120deg,#f1ede6 0%,#e2dcd2 45%,#c79a55 70%,#4a4f5a 100%)" role="img" aria-label="Electrician fitting a wall socket"></div>
<div class="project" style="left:789px;top:2544px;width:333px;height:244px;background:linear-gradient(150deg,#d87a2a 0%,#eef0f4 30%,#dfe4ec 65%,#9aa4b6 100%)" role="img" aria-label="Hands drawing on electrical blueprints with a multimeter"></div>
<div class="project" style="left:94px;top:2803px;width:504px;height:279px;background:linear-gradient(110deg,#c9d8ec 0%,#a9b9d2 40%,#c6d64a 70%,#6f7a5a 100%)" role="img" aria-label="Engineer with tablet beside a transmission tower"></div>
<div class="project" style="left:612px;top:2803px;width:506px;height:279px;background:linear-gradient(100deg,#3d5a8a 0%,#2a3f66 35%,#8bc23c 50%,#e0682a 58%,#2a3f66 72%,#1a2644 100%)" role="img" aria-label="Two engineers inspecting a switchgear room"></div>
<div class="slider-dots"><span class="on"></span><span></span><span></span></div>

<div class="news-band"></div>
<div class="news-head">
  <h2>NEWS &amp; <span class="accent">EVENTS</span><span class="mark"></span></h2>
  <span class="divider"></span>
</div>
<article class="news-main" role="img" aria-label="Two engineers in hard hats reviewing plans in a factory">
  <div class="caption">
    <h4>Lorem ipsum dolor sit amet consectetur</h4>
    <p>Sed do eiusmod tempor incididunt ut labore et dolore magna por incididunt ut labore et dolore magna</p>
  </div>
</article>
<article class="news-item" style="top:3367px">
  <div class="thumb" style="background:linear-gradient(165deg,#1a2458 0%,#2c3a80 35%,#e08a3a 60%,#3a3050 100%)" role="img" aria-label="Power pylon with light trails at night"></div>
  <div class="body"><span class="date-badge">20 MAY 2025</span><h5>Lorem ipsum dolor sit amet, consectetur adipiscing</h5><p>elit, sed do eiusmod tempor incididunt ut labore et dolore magna aliqua. Quis ipsum suspendisse ultrices gravida vel facilisis.</p></div>
</article>
<article class="news-item" style="top:3570px">
  <div class="thumb" style="background:linear-gradient(180deg,#1a2a70 0%,#3a6ae0 40%,#1f2a5a 65%,#0b1024 100%)" role="img" aria-label="Audience at a conference event"></div>
  <div class="body"><span class="date-badge">18 MAY 2025</span><h5>Lorem ipsum dolor sit amet, consectetur adipiscing</h5><p>elit, sed do eiusmod tempor incididunt ut labore et dolore magna aliqua. Quis ipsum suspendisse ultrices gravida vel facilisis.</p></div>
</article>

<section class="contact" role="img" aria-label="Electricians at work, navy overlay"></section>
<div class="contact-info">
  <p class="eyebrow">GETIN TOUCH</p>
  <h2>CONTACT US <span class="mark"></span></h2>
  <span class="divider"></span>
  <p class="lead">Fill out the contact form or call us at 1-555-014-2290 to schedule your consultation.</p>
  <div class="contact-line"><span class="icon-dot"><svg width="18" height="18" viewBox="0 0 24 24"><path fill="#273585" d="M6.6 10.8a15 15 0 0 0 6.6 6.6l2.2-2.2a1 1 0 0 1 1-.25 11.4 11.4 0 0 0 3.6.57 1 1 0 0 1 1 1V20a1 1 0 0 1-1 1A17 17 0 0 1 3 4a1 1 0 0 1 1-1h3.5a1 1 0 0 1 1 1c0 1.25.2 2.45.57 3.57a1 1 0 0 1-.25 1z"/></svg></span><span style="padding-top:6px">1-555-014-2290</span></div>
  <div class="contact-line"><span class="icon-dot"><svg width="18" height="18" viewBox="0 0 24 24"><path fill="#273585" d="M3 5h18v14H3zm2 2v.5l7 4.5 7-4.5V7z"/></svg></span><span style="padding-top:6px">hello@brisket-vane.example</span></div>
  <div class="contact-line"><span class="icon-dot"><svg width="18" height="18" viewBox="0 0 24 24"><path fill="#273585" d="M12 2a7 7 0 0 0-7 7c0 5 7 13 7 13s7-8 7-13a7 7 0 0 0-7-7zm0 9.5A2.5 2.5 0 1 1 12 6.5a2.5 2.5 0 0 1 0 5z"/></svg></span><span style="padding-top:6px">48 Larchmont Rd.<br>Eastbury NH 03999</span></div>
</div>
<form class="form-box">
  <div class="field" style="left:44px;top:40px;width:214px">&#9679; First Name</div>
  <div class="field" style="left:267px;top:40px;width:216px">&#9679; Last Name</div>
  <div class="field" style="left:44px;top:99px;width:439px">&#9993; Email address</div>
  <div class="field" style="left:44px;top:157px;width:439px">&#9742; Phone Number</div>
  <div class="field" style="left:44px;top:214px;width:439px;height:113px;align-items:flex-start;padding-top:15px">&#9679; Leave Message</div>
  <a class="btn btn-send">SEND MESSAGE &rsaquo;</a>
</form>

<svg class="abs" style="left:0;top:4420px" width="1200" height="190" viewBox="0 0 1200 190">
  <polygon fill="#f7941d" points="600,10 1200,80 1200,112 600,20"/>
  <polygon fill="#ffffff" points="0,160 600,20 1200,112 1200,190 0,190"/>
</svg>

<div class="footer-brand"><span class="brand-mark"></span>BRISKET &amp; VANE</div>
<div class="footer-rule" style="top:4672px"></div>
<nav class="footer-nav">
  <span>HOME</span><span class="sep"></span><span>ABOUT US</span><span class="sep"></span><span>SERVICES</span><span class="sep"></span><span>PROJECTS</span><span class="sep"></span><span>NEWS</span><span class="sep"></span><span>CONTACT</span>
</nav>
<div class="footer-rule" style="top:4745px"></div>

<div class="footer-contact" style="left:168px"><span class="circle"><svg width="16" height="16" viewBox="0 0 24 24"><path fill="#fff" d="M6.6 10.8a15 15 0 0 0 6.6 6.6l2.2-2.2a1 1 0 0 1 1-.25 11.4 11.4 0 0 0 3.6.57 1 1 0 0 1 1 1V20a1 1 0 0 1-1 1A17 17 0 0 1 3 4a1 1 0 0 1 1-1h3.5a1 1 0 0 1 1 1c0 1.25.2 2.45.57 3.57a1 1 0 0 1-.25 1z"/></svg></span><div><div class="k">Phone Number</div><div class="v">1-555-014-2290</div></div></div>
<div class="vsep" style="left:405px"></div>
<div class="footer-contact" style="left:451px"><span class="circle"><svg width="16" height="16" viewBox="0 0 24 24"><path fill="#fff" d="M3 5h18v14H3zm2 2v.5l7 4.5 7-4.5V7z"/></svg></span><div><div class="k">Email address</div><div class="v">hello@brisket-vane.example</div></div></div>
<div class="vsep" style="left:692px"></div>
<div class="footer-contact" style="left:732px"><span class="circle"><svg width="16" height="16" viewBox="0 0 24 24"><path fill="#fff" d="M12 2a7 7 0 0 0-7 7c0 5 7 13 7 13s7-8 7-13a7 7 0 0 0-7-7zm0 9.5A2.5 2.5 0 1 1 12 6.5a2.5 2.5 0 0 1 0 5z"/></svg></span><div><div class="k">Address</div><div class="v">48 Larchmont Rd. Eastbury NH 03999</div></div></div>

<footer class="bottom-bar">
  <p class="copyright">Copyright © 2025 <u>Brisket &amp; Vane</u>. All Right Reserved</p>
  <div class="socials"><span></span><span></span><span></span><span></span></div>
</footer>

</body>
</html>
```